Business Card Design Project

Business card based on attached logo

Todd Merrick
Todd@lorvantest.com
877-514-9073 ext. 318
Www.LorvanTest.com

Industry/Entity Type

Business

```html
<!DOCTYPE html>
<html lang="en">
<head>
<meta charset="utf-8">
<title>LorvanTest Business Card</title>
<link rel="stylesheet" href="https://fonts.googleapis.com/css2?family=Open+Sans:wght@400;600;700&display=swap">
<style>
  :root {
    --page-bg: #d9d9dc;
    --card-dark: #1f1f1f;
    --card-light: #ffffff;
    --ink-light: #ffffff;
    --ink-dark: #2a2a2a;
    --accent: #e8242c;
    --muted: #e6e6e6;
  }
  * { margin: 0; padding: 0; box-sizing: border-box; }
  html, body {
    width: 1200px;
    height: 960px;
    overflow: hidden;
    background: var(--page-bg);
    font-family: "Open Sans", Arial, sans-serif;
  }
  .sheet {
    position: relative;
    width: 1200px;
    height: 960px;
  }
  .card {
    position: absolute;
    left: 250px;
    width: 700px;
    height: 400px;
    box-shadow: 0 10px 30px rgba(0,0,0,0.18);
  }
  .card--front { top: 60px; background: var(--card-dark); color: var(--ink-light); }
  .card--back  { top: 500px; background: var(--card-light); color: var(--ink-dark); }

  .brand {
    position: absolute;
    display: flex;
    align-items: center;
    gap: 14px;
    font-weight: 700;
    letter-spacing: 0.5px;
  }
  .brand__square {
    width: 22px;
    height: 22px;
    background: var(--accent);
  }
  .card--front .brand {
    left: 64px;
    top: 86px;
    font-size: 62px;
    color: var(--ink-light);
  }
  .card--back .brand {
    left: 0;
    right: 0;
    top: 0;
    bottom: 0;
    justify-content: center;
    font-size: 58px;
    color: var(--ink-dark);
  }

  .holder {
    position: absolute;
    right: 48px;
    top: 218px;
    text-align: right;
  }
  .holder__name { font-size: 24px; font-weight: 600; line-height: 1.1; }
  .holder__role { font-size: 13px; font-weight: 600; margin-top: 2px; }

  .contacts {
    position: absolute;
    right: 48px;
    top: 290px;
    list-style: none;
    text-align: right;
    font-size: 14px;
    line-height: 20px;
    color: var(--muted);
  }
  .contacts li {
    display: flex;
    justify-content: flex-end;
    align-items: center;
    gap: 8px;
  }
  .contacts svg { width: 10px; height: 10px; fill: var(--accent); flex: none; }
</style>
</head>
<body>
<main class="sheet">
  <section class="card card--front" aria-label="Card front">
    <div class="brand"><span>LorvanTest</span><span class="brand__square"></span></div>

    <div class="holder">
      <p class="holder__name">Todd Merrick</p>
      <p class="holder__role">Owner</p>
    </div>

    <ul class="contacts">
      <li>P O Box 5821, Millbrook AU
        <svg viewBox="0 0 10 10" aria-hidden="true"><path d="M5 0.5 L10 5 H8.5 V9.5 H6 V6.5 H4 V9.5 H1.5 V5 H0 Z"/></svg>
      </li>
      <li>877-514-9073 ext. 318
        <svg viewBox="0 0 10 10" aria-hidden="true"><path d="M2 0.5 L3.8 0.5 L4.4 3 L3.2 4 C3.8 5.3 4.7 6.2 6 6.8 L7 5.6 L9.5 6.2 L9.5 8 C9.5 8.9 8.8 9.5 8 9.5 C4 9.2 0.8 6 0.5 2 C0.5 1.2 1.1 0.5 2 0.5 Z"/></svg>
      </li>
      <li>Todd@lorvantest.com
        <svg viewBox="0 0 10 10" aria-hidden="true"><path d="M0 2 H10 V8.5 H0 Z M0.6 2.4 L5 5.8 L9.4 2.4 Z" fill-rule="evenodd"/></svg>
      </li>
      <li>www.lorvantest.com
        <svg viewBox="0 0 10 10" aria-hidden="true"><circle cx="5" cy="5" r="4.6"/></svg>
      </li>
    </ul>
  </section>

  <section class="card card--back" aria-label="Card back">
    <div class="brand"><span>LorvanTest</span><span class="brand__square"></span></div>
  </section>
</main>
</body>
</html>
```